Elevating our current Business Card Design

We want to elevate our current business card with a new design to look like a zenith 300 company. We are a premium lubricant distributor (oil and grease).
We need 2 versions, version 1 is as per the uploaded a copy of our current business card with the English version.
For our Chinese version we need to use the front to be English in English and have the back of the card designed exactly like the front for all info to be in Chinese.
The design template needs to be such that we can amend the template with adding different information for each person's card.
The background colour of the card can be changed- we just need to clearly see all information on the card and logos.
The QJR and Ember steady logos cannot have any colour or display changes- only use the logos attached.
All logos need to be included and all information from the attached current card

```html
<!DOCTYPE html>
<html lang="en">
<head>
<meta charset="utf-8">
<title>Vantoro – Business Card</title>
<link href="https://fonts.googleapis.com/css2?family=Open+Sans:wght@400;600&family=Ubuntu:ital,wght@1,500&display=swap" rel="stylesheet">
<style>
  :root{
    --stage:#242424;
    --ink:#1f1f22;
    --paper:#fdfdf7;
    --brand-red:#e32722;
    --gold:#e9a91c;
    --badge-neutral:#5a5a60;
    --text-light:#f4f4f4;
  }
  *{box-sizing:border-box;margin:0;padding:0}
  html,body{width:1200px;height:780px;overflow:hidden;background:var(--stage)}
  .stage{width:1200px;height:780px;display:flex;align-items:center;justify-content:center;gap:30px}
  .card{position:relative;width:560px;height:320px;border-radius:16px;overflow:hidden;font-family:"Open Sans",sans-serif}
  .card-front{background:var(--paper)}
  .card-back{background:var(--ink);display:flex;align-items:center;justify-content:center}
  .card-art{position:absolute;inset:0;width:100%;height:100%}
  .holder{position:absolute;left:22px;top:14px}
  .holder-name{font-family:"Ubuntu",sans-serif;font-style:italic;font-weight:500;font-size:25px;color:var(--brand-red);line-height:1.1}
  .holder-title{font-size:12px;color:var(--ink);margin-top:2px}
  .address{position:absolute;left:22px;top:112px;color:var(--text-light);font-size:11.5px;line-height:16px;font-style:normal}
  .contacts{position:absolute;left:22px;top:154px;list-style:none;color:var(--text-light);font-size:11.5px;line-height:16px}
  .contacts li{display:flex;align-items:center;gap:7px}
  .contacts svg{width:10px;height:10px;flex:none}
  .brand-word{font-family:"Open Sans",sans-serif;font-weight:600;color:var(--brand-red);display:flex;align-items:center;gap:12px}
  .brand-word .dot{border-radius:50%;background:var(--gold);flex:none}
  .front-brand{position:absolute;right:38px;top:92px;font-size:42px}
  .front-brand .dot{width:18px;height:18px}
  .back-brand{font-size:72px}
  .back-brand .dot{width:30px;height:30px}
</style>
</head>
<body>
<main class="stage">

  <section class="card card-front" aria-label="Business card front">
    <svg class="card-art" viewBox="0 0 560 320" aria-hidden="true">
      <path class="swoosh-red" fill="var(--brand-red)" d="M0,92 C80,66 150,74 190,112 C228,150 226,214 278,240 C336,268 440,252 560,236 L560,320 L0,320 Z"/>
      <path class="wave-dark" fill="var(--ink)" d="M0,92 C80,66 150,74 190,112 C226,148 220,230 280,256 C342,282 440,268 560,256 L560,320 L0,320 Z"/>
      <g class="certifications">
        <circle class="badge-ember" cx="262" cy="283" r="14" fill="var(--badge-neutral)"/>
        <circle class="badge-qjr" cx="308" cy="283" r="14" fill="var(--badge-neutral)"/>
        <circle class="badge-qjr" cx="346" cy="283" r="14" fill="var(--badge-neutral)"/>
        <circle class="badge-qjr" cx="384" cy="283" r="14" fill="var(--badge-neutral)"/>
        <rect class="badge-partner" x="410" y="268" width="122" height="32" rx="3" fill="var(--badge-neutral)"/>
      </g>
    </svg>

    <div class="holder">
      <p class="holder-name">Marina Castell</p>
      <p class="holder-title">Administration Executive</p>
    </div>

    <address class="address">
      48 Harbourline Drive<br>Maddox, WA 6210
    </address>

    <ul class="contacts">
      <li><svg viewBox="0 0 10 10"><path fill="var(--brand-red)" d="M2,0 L4,2 L3,3.5 Q4.5,6 6.5,7 L8,6 L10,8 L8.5,10 Q3,9 0,1.5 Z"/></svg>1300 402 617</li>
      <li><svg viewBox="0 0 10 10"><rect x="2.5" y="0.5" width="5" height="9" rx="1" fill="none" stroke="var(--brand-red)"/></svg>+61 412 880 394</li>
      <li><svg viewBox="0 0 10 10"><rect x="0.5" y="4" width="9" height="5" fill="var(--brand-red)"/><rect x="2.5" y="0.5" width="5" height="3.5" fill="none" stroke="var(--brand-red)"/></svg>+61 8 9504 2261</li>
      <li><svg viewBox="0 0 10 10"><circle cx="5" cy="5" r="4.5" fill="none" stroke="var(--brand-red)"/><path d="M0.5,5 H9.5 M5,0.5 Q2,5 5,9.5 Q8,5 5,0.5" fill="none" stroke="var(--brand-red)" stroke-width="0.8"/></svg>www.vantorodirect.com</li>
      <li><svg viewBox="0 0 10 10"><rect x="0.5" y="2" width="9" height="6.5" fill="var(--brand-red)"/><path d="M0.5,2 L5,6 L9.5,2" fill="none" stroke="var(--ink)" stroke-width="0.8"/></svg>marina.castell@vantorodirect.com</li>
    </ul>

    <div class="brand-word front-brand"><span class="dot"></span>Vantoro</div>
  </section>

  <section class="card card-back" aria-label="Business card back">
    <div class="brand-word back-brand"><span class="dot"></span>Vantoro</div>
  </section>

</main>
</body>
</html>
```